International oil and gas consultancy business needs a web design

Hello, I need a web design for a new oil and gas auditing consultancy business. My business undertakes contract audit assignments to review past costs of oil and gas operations (see attached Excel file for more details of the businesses services). I need the design to give the impression of a professional consultancy style of business, rather than a retail style of website. Note: this job is for LAYOUT DESIGN ONLY and not coding / development work.
The following are my key design principles:
1. BASIC DESIGN: I am after a simple and static web design. I don't want the pages busy or cluttered with too many images or detail.
2. HORIZONTAL TABS: I require a horizontal set of tabs towards the top of the screens (see Excel file) which remain in the same position on every page.
3. META TAG PLANNING: The design should allow for effective positioning of content so that key meta tag words can easily be built during the technical build stage.
4. NUMBER OF PAGES: The site will eventually have a maximum of 10 pages. Seven of the pages will reside under the tabs. Can you please present your opening submission for the first two page.
5. USE OF MY LOGO: The attached logo (JPEG file) should be used throughout the website. Please don't change the shape and colour.
6. COLOUR SCHEMES: Can you please consider any of the 3 colour schemes below:
A - dark red (to match the logo), light grey and perhaps another of your liking;
B - dark red (to match the logo), light cream and perhaps another of your liking;
C - dark red (to match the logo), white and perhaps another of your liking.
7. WORD CONTENT: I have attached an Excel file which shows the estimated word content for each page.
8. FUTURE USE OF DESIGN: I'm planning on building a Wordpress website. Can you please ensure the layout design supports this application.

Target Market(s)

oil and gas companies (small and large)

Industry/Entity Type

Oil And Gas

Font styles to use
Sans Serif

Requirements
Nice to have
• The KRL logo and business name should ideally be next to each other. Also, the logo and name should be part of the background graphics, not above it.

```html
<!DOCTYPE html>
<html lang="en">
<head>
<meta charset="utf-8">
<title>KRL – Kestrel Ridge Auditing</title>
<link href="https://fonts.googleapis.com/css2?family=Open+Sans:wght@400;600&family=Roboto:wght@400;500&display=swap" rel="stylesheet">
<style>
  :root{
    --red:#8e1418;
    --red-dark:#6e0d10;
    --red-light:#a8191e;
    --text:#3a3a3a;
    --heading:#222;
    --news-bg:#ede2e2;
    --rule:#c9b8b8;
    --footer:#2b2b2b;
    --footer-text:#bdbdbd;
    --btn-dark:#1f1f1f;
  }
  *{box-sizing:border-box;margin:0;padding:0}
  html,body{width:1050px;height:1200px;overflow:hidden;background:#fff}
  body{position:relative;font-family:"Open Sans",Arial,sans-serif;color:var(--text)}
  .abs{position:absolute}

  /* header */
  .brand{left:158px;top:22px;display:flex;align-items:center;gap:10px}
  .brand-mark{width:14px;height:14px;background:var(--red)}
  .brand-name{font-family:"Open Sans",Arial,sans-serif;font-weight:600;color:var(--red);font-size:40px;line-height:1;letter-spacing:1px}
  .brand-sub{left:166px;top:68px;font-size:11px;font-weight:600;color:var(--red)}
  .social{right:158px;top:46px;display:flex;gap:10px}
  .social span{width:14px;height:14px;border-radius:50%;background:#8a8a8a;display:block}

  /* navigation */
  .nav{left:0;top:94px;width:1050px;height:40px;background:linear-gradient(#a21a1f,var(--red-dark))}
  .nav ul{list-style:none;display:flex;position:absolute;left:158px;top:0;height:40px}
  .nav li{height:40px;line-height:40px;font-size:11px;color:#fff;padding:0 22px;margin-right:4px}
  .nav li.active{background:rgba(0,0,0,.18)}

  /* slider */
  .slider{left:157px;top:149px;width:736px;height:394px;border:2px solid #e2e2e2;padding:3px}
  .slide{width:100%;height:100%;background:linear-gradient(100deg,#d9dce2 0%,#cfd2d8 45%,#b9323a 62%,#d5d7dc 80%,#c8cad0 100%);position:relative}
  .slide-caption{position:absolute;left:0;bottom:0;width:100%;height:53px;background:rgba(255,255,255,.78);color:var(--red);font-weight:600;font-size:14px;line-height:53px;padding-left:28px}
  .arrow{position:absolute;top:180px;width:20px;height:20px;border-radius:50%;background:#555;opacity:.85}
  .arrow svg{display:block}
  .arrow.prev{left:13px}.arrow.next{right:13px}

  /* welcome */
  .welcome-title{left:159px;top:572px;font-family:"Roboto",Arial,sans-serif;font-size:19px;color:var(--heading)}
  .accent{color:var(--red)}
  .welcome-img{left:158px;top:609px;width:484px;height:163px;background:linear-gradient(120deg,#d8d8d8,#b7b7b7 55%,#e6e6e6)}
  .welcome-text{left:158px;top:786px;width:490px;font-size:10px;line-height:18px}
  .btn{display:inline-block;color:#fff;font-size:11px;text-align:center;border-radius:2px}
  .btn-red{left:158px;top:853px;width:114px;height:37px;line-height:37px;background:linear-gradient(var(--red-light),var(--red-dark))}

  /* news */
  .news{left:658px;top:573px;width:234px;height:317px;background:var(--news-bg)}
  .news-head{height:49px;background:linear-gradient(var(--red-light),var(--red-dark));color:#fff;font-family:"Roboto",Arial,sans-serif;font-size:18px;line-height:49px;padding-left:22px}
  .news-item{margin:0 19px;padding:19px 0 8px;border-bottom:1px solid var(--rule)}
  .news-item:first-of-type{padding-top:19px}
  .news-date{font-size:10.5px;color:var(--red);line-height:14px}
  .news-text{font-size:10.5px;color:#333;line-height:15px;margin-top:2px}
  .news-more{text-align:center;font-size:10.5px;font-weight:600;color:var(--red);margin-top:20px}

  /* services */
  .service{top:930px;width:240px}
  .service h3{font-family:"Roboto",Arial,sans-serif;font-weight:400;font-size:18px;color:var(--heading);margin-bottom:9px}
  .service p{font-size:9.5px;line-height:18px;color:#555;padding-left:1px}
  .btn-dark{position:absolute;top:134px;left:0;width:94px;height:36px;line-height:36px;background:linear-gradient(#3a3a3a,var(--btn-dark))}

  /* footer */
  .footer{left:0;top:1130px;width:1050px;height:70px;background:var(--footer);color:var(--footer-text);font-size:9.5px}
  .footer .copy{position:absolute;left:158px;top:29px}
  .footer .links{position:absolute;right:158px;top:29px}
  .footer .sep{margin:0 12px}
</style>
</head>
<body>
  <header>
    <div class="abs brand"><span class="brand-name">KRL</span><span class="brand-mark"></span></div>
    <div class="abs brand-sub">Kestrel Ridge Auditing</div>
    <div class="abs social" aria-label="Social links"><span></span><span></span><span></span><span></span></div>
  </header>

  <nav class="abs nav">
    <ul>
      <li class="active">HOME</li>
      <li>ABOUT US</li>
      <li>SERVICES</li>
      <li>OUR PARTNERS</li>
      <li>APPROACH</li>
      <li>WHY CHOOSE US</li>
      <li>CONTACT US</li>
    </ul>
  </nav>

  <section class="abs slider">
    <div class="slide" role="img" aria-label="Auditor working at a desk with a calculator in a bright office">
      <span class="arrow prev"><svg width="20" height="20"><path d="M11.5 6 7.5 10l4 4" fill="none" stroke="#fff" stroke-width="2"/></svg></span>
      <span class="arrow next"><svg width="20" height="20"><path d="M8.5 6l4 4-4 4" fill="none" stroke="#fff" stroke-width="2"/></svg></span>
      <div class="slide-caption">Lorem ipsum dolor sit amet, consectetuer adipiscing elit, sed diam nonummy nibh euismod</div>
    </div>
  </section>

  <h1 class="abs welcome-title">Welcome To <span class="accent">Kestrel Ridge Auditing</span></h1>
  <div class="abs welcome-img" role="img" aria-label="Financial spreadsheets with a stopwatch lying on top"></div>
  <p class="abs welcome-text">Kestrel Ridge Auditing is a Perth (Australia) based firm specialising in providing quality audit services for the oil and gas industry. Our skills and knowledge of oil and gas, along with a deep understanding of business commercial needs, ensures the high quality of our services</p>
  <a class="abs btn btn-red">Read More</a>

  <aside class="abs news">
    <div class="news-head">Latest News</div>
    <div class="news-item"><div class="news-date">15 AUG 2014</div><div class="news-text">Lorem ipsum dolor sit amet, consecte tuer adipiscing elit, sed diam nibh</div></div>
    <div class="news-item"><div class="news-date">14 AUG 2014</div><div class="news-text">Ut wisi enim ad minim veniam, quis nostrud exerci tation ullamcorper</div></div>
    <div class="news-item"><div class="news-date">13 AUG 2014</div><div class="news-text">Claritas est etiam processus dynamic us, qui sequitur mutationem</div></div>
    <div class="news-more">VIEW MORE NEWS</div>
  </aside>

  <section class="abs service" style="left:158px">
    <h3>Joint Venture <span class="accent">Audits</span></h3>
    <p>Ut wisi enim ad minim veniam, quis nostrud exerci tation ullamcorper suscipit lobortis nisl ut aliquip ex ea commodo consequat. Duis autem vel eum iriure dolor in hendrerit in vulputate velit esse molestie consequat.</p>
    <a class="btn btn-dark">View Details</a>
  </section>
  <section class="abs service" style="left:407px">
    <h3>Contract <span class="accent">Audits</span></h3>
    <p>Ut wisi enim ad minim veniam, quis nostrud exerci tation ullamcorper suscipit lobortis nisl ut aliquip ex ea commodo consequat. Duis autem vel eum iriure dolor in hendrerit in vulputate velit esse molestie consequat.</p>
    <a class="btn btn-dark">View Details</a>
  </section>
  <section class="abs service" style="left:658px">
    <h3>Operations <span class="accent">Audits</span></h3>
    <p>Ut wisi enim ad minim veniam, quis nostrud exerci tation ullamcorper suscipit lobortis nisl ut aliquip ex ea commodo consequat. Duis autem vel eum iriure dolor in hendrerit in vulputate velit esse molestie consequat.</p>
    <a class="btn btn-dark">View Details</a>
  </section>

  <footer class="abs footer">
    <div class="copy">Copyright c 2014 Kestrel Ridge Auditing. ALl Right Reserved.</div>
    <div class="links">Terms and Conditions<span class="sep">|</span>Privacy policy</div>
  </footer>
</body>
</html>
```